KBT Business Cards

We require business cards for our business. We would like a matte black back to the card, with our logo centred in the middle. The front side of the card is open to design.

Target Market(s)

Clients looking for legal services (professional)

Industry/Entity Type

Legal

Contact Information for Business Card

Doran Kelbrath
Partner
Mobile: 0461 738 524
Email: doran@kbtlaw.co
Website: www.kbtlaw.co
Level 3, 118 Wendmore Street
Sydney NSW 2000

Font styles to use
Other font styles liked:
• Avenir

Colors
f04a50
ffffff
1b1b1b

Requirements
Must have
• Black back with logo included in the centre of the card.
• Our font is Avenir.

```html
<!DOCTYPE html>
<html lang="en">
<head>
<meta charset="utf-8">
<title>KBT Legal – Business Cards</title>
<link href="https://fonts.googleapis.com/css2?family=Nunito+Sans:wght@400;700;800&display=swap" rel="stylesheet">
<style>
  :root {
    --accent: #d81e4a;
    --white: #ffffff;
    --card-dark: #1b1b1b;
    --card-mid: #3a3a3a;
    --text-soft: #e6e6e6;
    --divider: #5a5a5a;
    --stage-light: #dcdddf;
    --stage-dark: #a3a4a7;
  }
  * { margin: 0; padding: 0; box-sizing: border-box; }
  html, body {
    width: 1106px; height: 1200px; overflow: hidden;
    font-family: "Nunito Sans", "Avenir", sans-serif;
  }
  body {
    position: relative;
    background: linear-gradient(90deg, var(--stage-light) 0%, #c4c5c7 55%, var(--stage-dark) 100%);
  }
  .card {
    position: absolute;
    left: 135px;
    width: 835px;
    height: 477px;
    background: radial-gradient(ellipse at 50% 55%, var(--card-mid) 0%, #262626 50%, var(--card-dark) 100%);
    clip-path: polygon(96px 0, 100% 0, 100% 385px, 740px 100%, 0 100%, 0 92px);
  }
  .card--front { top: 99px; }
  .card--back  { top: 619px; }

  .brand { position: absolute; display: flex; align-items: center; }
  .brand__mark { background: var(--accent); flex: none; }
  .brand__name {
    color: var(--white); font-weight: 700; line-height: 1.05;
    text-transform: uppercase; letter-spacing: 0.02em;
  }

  .card--front .brand { left: 56px; top: 185px; gap: 22px; }
  .card--front .brand__mark { width: 96px; height: 96px; }
  .card--front .brand__name { font-size: 33px; }

  .divider {
    position: absolute; left: 432px; top: 107px;
    width: 2px; height: 265px; background: var(--divider);
  }
  .contact { position: absolute; left: 468px; top: 104px; color: var(--text-soft); }
  .contact__name {
    color: var(--accent); font-weight: 800; font-size: 29px;
    text-transform: uppercase; letter-spacing: 0.01em; line-height: 1.1;
  }
  .contact__role { font-size: 21px; text-transform: uppercase; letter-spacing: 0.04em; margin-top: 2px; }
  .contact__address { font-size: 21px; line-height: 32px; margin-top: 26px; }
  .contact__list { list-style: none; margin-top: 20px; }
  .contact__list li {
    display: flex; align-items: center; gap: 10px;
    font-size: 21px; line-height: 36px;
  }
  .contact__list svg { width: 22px; height: 22px; flex: none; }

  .card--back .brand { left: 150px; top: 126px; gap: 48px; }
  .card--back .brand__mark { width: 180px; height: 180px; }
  .card--back .brand__name { font-size: 56px; }

  .web {
    position: absolute; left: 0; right: 0; top: 426px;
    text-align: center; color: var(--text-soft);
    font-size: 21px; letter-spacing: 0.3em;
  }
  .web__domain { color: var(--accent); font-weight: 700; }
</style>
</head>
<body>

  <section class="card card--front">
    <div class="brand">
      <span class="brand__mark"></span>
      <span class="brand__name">KBT Legal</span>
    </div>

    <div class="divider"></div>

    <div class="contact">
      <p class="contact__name">Doran Kelbrath</p>
      <p class="contact__role">Partner</p>
      <p class="contact__address">Level 3, 118 Wendmore Street<br>Sydney NSW 2000</p>
      <ul class="contact__list">
        <li>
          <svg viewBox="0 0 22 22" aria-hidden="true">
            <circle cx="11" cy="11" r="9.5" fill="none" stroke="var(--accent)" stroke-width="1.6"/>
            <rect x="7.5" y="5" width="7" height="12" rx="1.2" fill="none" stroke="var(--accent)" stroke-width="1.5"/>
          </svg>
          0461 738 524
        </li>
        <li>
          <svg viewBox="0 0 22 22" aria-hidden="true">
            <rect x="1" y="5" width="20" height="13" fill="var(--accent)"/>
            <path d="M1 5 L11 13 L21 5 M1 18 L8.5 11 M21 18 L13.5 11" fill="none" stroke="var(--card-dark)" stroke-width="1.3"/>
          </svg>
          doran@kbtlaw.co
        </li>
        <li>
          <svg viewBox="0 0 22 22" aria-hidden="true" fill="none" stroke="var(--accent)" stroke-width="1.5">
            <circle cx="11" cy="11" r="9.5"/>
            <ellipse cx="11" cy="11" rx="4.2" ry="9.5"/>
            <path d="M1.5 11 H20.5 M3.5 6 H18.5 M3.5 16 H18.5"/>
          </svg>
          www.kbtlaw.co
        </li>
      </ul>
    </div>
  </section>

  <section class="card card--back">
    <div class="brand">
      <span class="brand__mark"></span>
      <span class="brand__name">KBT Legal</span>
    </div>
    <p class="web">www.<span class="web__domain">kbtlaw</span>.co</p>
  </section>

</body>
</html>
```